Modern/Bold/Unique Prenatal Vitamin label redesign

We are in need of a design update for our Prenatal Vitamin label. We want to modernize our label and give it a fresh feel.
It should bring a feeling of fun, joy, and sophistication, but also be bold/edgy/unique and portray Trust and Authority. Our buyers are mainly mothers in the age range of 25-34 who are pregnant or breastfeeding.
I will attach our current label design, as well as some inspiration to go off of.
We like the idea of having a clean, easy to read label label with bold/vibrant colors and fonts. We like the idea of having some retro vibes in it as well
Please see the attached artwork for design inspiration (New Design Idea). We like the idea of having a pregnant mother image like the attachment on the label, with the rest of the label being white. Please come up with a unique drawing/image for the design. We cannot use a copied image or stock image.
We look forward to working with you!

```html
<!DOCTYPE html>
<html lang="en">
<head>
<meta charset="utf-8">
<title>Nestbloom Prenatal Bloom Label</title>
<link rel="stylesheet" href="https://fonts.googleapis.com/css2?family=Fredoka:wght@500;600&display=swap">
<style>
  :root {
    --page: #ffffff;
    --pink-top: #fd6485;
    --pink-bottom: #ee2a4a;
    --heart-glow: #b8001c;
    --blue: #0277bd;
    --yellow: #f4f20a;
    --white: #ffffff;
    --badge: #f9d5bf;
    --badge-blue: #1d6fb0;
    --badge-red: #ee2a4a;
    --splash-pink: #ec1f7a;
    --splash-orange: #f7861e;
    --splash-teal: #1cb8d6;
    --splash-green: #49b94a;
    --splash-navy: #1f4f7a;
  }
  html, body {
    margin: 0;
    padding: 0;
    width: 1099px;
    height: 1200px;
    overflow: hidden;
    background: var(--page);
  }
  .canvas {
    position: relative;
    width: 1099px;
    height: 1200px;
  }
  .label {
    position: absolute;
    left: 110px;
    top: 56px;
    width: 880px;
    height: 1087px;
    overflow: hidden;
    background: linear-gradient(180deg, var(--pink-top) 0%, var(--pink-bottom) 75%);
    font-family: "Fredoka", sans-serif;
    color: var(--white);
  }
  .brand {
    position: absolute;
    top: 30px;
    left: 0;
    width: 100%;
    text-align: center;
    font-weight: 600;
    font-size: 100px;
    line-height: 1;
    letter-spacing: 1px;
    color: var(--white);
  }
  .heart {
    position: absolute;
    left: 77px;
    top: 247px;
    width: 726px;
    height: 578px;
    filter: drop-shadow(0 0 28px var(--heart-glow));
  }
  .base-band {
    position: absolute;
    left: 0;
    top: 0;
    width: 880px;
    height: 1087px;
  }
  .mother-art {
    position: absolute;
    left: 0;
    top: 0;
    width: 880px;
    height: 1087px;
  }
  .product {
    position: absolute;
    left: 0;
    width: 100%;
    text-align: center;
    margin: 0;
  }
  .product-name {
    top: 878px;
    font-weight: 600;
    font-size: 70px;
    line-height: 1;
  }
  .product-tagline {
    top: 954px;
    font-weight: 500;
    font-size: 37px;
    line-height: 1;
    color: var(--yellow);
    letter-spacing: -0.5px;
  }
  .product-for {
    top: 1000px;
    font-weight: 500;
    font-size: 50px;
    line-height: 1;
  }
  .count-badge {
    position: absolute;
    left: 689px;
    top: 732px;
    width: 146px;
    height: 146px;
    border-radius: 50%;
    background: var(--badge);
    text-align: center;
  }
  .count-badge::before {
    content: "";
    position: absolute;
    inset: 14px;
    border-radius: 50%;
    border: 1.5px solid var(--white);
  }
  .count-badge .badge-top,
  .count-badge .badge-bottom {
    position: absolute;
    left: 0;
    width: 100%;
    font-weight: 500;
    font-size: 17px;
    color: var(--badge-blue);
    line-height: 1;
  }
  .badge-top { top: 18px; }
  .badge-bottom { top: 114px; }
  .count-badge .badge-number {
    position: absolute;
    left: 0;
    top: 34px;
    width: 100%;
    font-weight: 600;
    font-size: 74px;
    line-height: 1;
    color: var(--badge-red);
  }
</style>
</head>
<body>
<main class="canvas">
  <section class="label">
    <div class="brand">Nestbloom</div>

    <svg class="heart" viewBox="0 0 726 578" aria-hidden="true">
      <path d="M363 578 L60 260 C-20 170 10 20 140 5 C240 -5 300 40 363 95 C426 40 486 -5 586 5 C716 20 746 170 666 260 Z" fill="var(--white)"/>
    </svg>

    <svg class="base-band" viewBox="0 0 880 1087" aria-hidden="true">
      <path d="M0 895 Q440 760 880 895 L880 1087 L0 1087 Z" fill="var(--blue)"/>
    </svg>

    <svg class="mother-art" viewBox="0 0 880 1087" role="img" aria-label="Illustration of a pregnant mother in profile cradling her belly, made of colourful paint splashes flowing across the heart">
      <defs>
        <radialGradient id="figureGlow" cx="0.42" cy="0.5" r="0.6">
          <stop offset="0" stop-color="var(--splash-orange)"/>
          <stop offset="0.3" stop-color="var(--splash-pink)"/>
          <stop offset="0.6" stop-color="var(--splash-teal)"/>
          <stop offset="0.85" stop-color="var(--splash-green)" stop-opacity="0.5"/>
          <stop offset="1" stop-color="var(--splash-teal)" stop-opacity="0"/>
        </radialGradient>
        <radialGradient id="splashLeft" cx="0.5" cy="0.5" r="0.5">
          <stop offset="0" stop-color="var(--splash-pink)" stop-opacity="0.55"/>
          <stop offset="0.6" stop-color="var(--splash-teal)" stop-opacity="0.3"/>
          <stop offset="1" stop-color="var(--splash-teal)" stop-opacity="0"/>
        </radialGradient>
        <radialGradient id="splashRight" cx="0.5" cy="0.5" r="0.5">
          <stop offset="0" stop-color="var(--splash-orange)" stop-opacity="0.5"/>
          <stop offset="0.6" stop-color="var(--splash-pink)" stop-opacity="0.25"/>
          <stop offset="1" stop-color="var(--splash-pink)" stop-opacity="0"/>
        </radialGradient>
      </defs>
      <ellipse cx="200" cy="420" rx="150" ry="190" fill="url(#splashLeft)"/>
      <ellipse cx="700" cy="560" rx="110" ry="230" fill="url(#splashRight)"/>
      <ellipse cx="420" cy="640" rx="200" ry="290" fill="url(#figureGlow)"/>
    </svg>

    <div class="count-badge">
      <span class="badge-top">VEGGIE</span>
      <span class="badge-number">90</span>
      <span class="badge-bottom">CAPSULES</span>
    </div>

    <h1 class="product product-name">Prenatal Bloom</h1>
    <p class="product product-tagline">Once Daily Premium Multivitamin For</p>
    <p class="product product-for">Mama &amp; Baby</p>
  </section>
</main>
</body>
</html>
```